Flyer for an pediatric sleep consultancy - to distribute to play and childcare centers etc.

I need a flyer that will attract the attention of parents with children between the age of babies to toddlers, who may be experiencing sleep issues. The flyer will be placed at places such as community centers, doctors room, play centers, kindergardens, etc.

My company is called "The Quiet Meadow Nest" and provides a sleep consultancy service. My service essentially provides a customized plan for parents to follow and general advice and guidance. It is not medical advice.

I like to the flyer to have an overall tone that is soft and peaceful with a clean and beautiful design, however can catch the attention of parents who may be struggling with their child's sleep issues and are sleep deprived. I would like photos with minimal text. The colour I use is a brownish rose. I will attach some of my designs to give you an idea. You can have a look at my homepage as well to get an idea about my esthetic direction and the colour. Although the colour of my page is a bit too brownish....

I will provide the text to appear in the flyer once I have a better idea of the layout that I prefer for the flyer. The text however wont be extensive, just some catchy points.

I want to direct people to my website which is www.quietmeadownest-example.com
I offer a first FREE evaluation call, to the parents, to get to know each other better, learn about their child's particular sleep problems and see if we are a good fit and can work together. I would like to have this information somehow on the flyer, so that the parents will contact me.
I also have a facebook page, which is: The Quiet Meadow Nest

I have a logo that I would like to appear on the flyer. I will attach the file once the uploader on pixel guild is fixed.

When I print the flyer - I like to print A5 SIZE ... please make sure the formatting is OK for this size.

Here are some text ideas. of course all of it would be too much, I guess. On the front of the flyer I would like to have some catchy phrase or something similar to get people interested and to want to know more. On the back there could be a bit more text and information. But I'm open too suggestions....
I'm not too sure about the wording yet. But here are some text that I might be use:

Is sleep an issue in your home?

Is your baby having trouble sleeping? ... are you?!
I can help!

Sleep, baby, sleep….

Teaching children how to sleep

The Quiet Meadow Nest is a pediatric sleep consultancy that specializes in helping parents with children who struggle to develop good and healthy sleep habits.
Disruptive sleep patterns or not enough sleep can affect the physical, mental and emotional development of your child.

Of course nobody plans to have a sleep problem, but habits can become easily ingrained and spiral quickly out of control and you can find yourself sleep deprived, desperate and not too sure what to do. You see all the other sleeping babies and wish there was someone who understood what you were going through?! Well, there is!

Contact me for a free 15 minute consultation.

This 15 minute „mini“ consultation is a chance to discuss your unique sleep challenges and sleep goals with me. I will provide you with an overview of how I will work with your family to achieve your wildest sleep dreams (goals).
Furthermore do I understand and believe that every child and their family is unique and there is no one size fits all!
I would love to have a chat with you and talk about how I can help make things easier for you and your family!

Do I need a sleep consultant for my child?
The answer is yes if:
- if your child will only fall asleep when nursing or bottle feeding
- if your child needs a dummy or other external aid, like being rocked, patted or taken for a care ride to fall asleep
- if your good night routine is a challenging and exhausting procedure instead of a relaxed and enjoyable moment for the whole family
- if sleep is a constant battle in your home which leaves you feeling frustrated and exhausted
- if your own lack of sleep is taking a toll on you and the whole family

What can I do for you?

I will:

- Guide you to set an age appropriate foundation for good sleep
- Create an individual sleep plan tailored especially to your child’s sleep needs and circumstances
- Help you to teach your childto go to sleep and get back to sleep independently during the night
- show you how to teach your child to take healthful, restorative naps
-Learn

Contact:

Marta Lindqvist
info@quietmeadownest-example.com
www.quietmeadownest-example.com
+34 612 384 705

Consultations in English, German or Spanish via Phone/Skype or home consultation
Updates

Project Deadline Extended
Reason: I have to go on a business trip and won't be able to choose a design until the deadline. During the trip I won't have time to give feedback and ask for changes. thank you

Target Market(s)

parents, sleep deprived mothers, young families, child care provider,

Industry/Entity Type

Baby Care

Contact Information for Business Card

Marta Lindqvist
pediatric sleep consultant
+34 612 384 705

```html
<!DOCTYPE html>
<html lang="en">
<head>
<meta charset="utf-8">
<title>The Quiet Meadow Nest – A5 Flyer</title>
<link href="https://fonts.googleapis.com/css2?family=Open+Sans:ital,wght@0,300;0,400;0,600;1,400;1,600&display=swap" rel="stylesheet">
<style>
  :root{
    --rose:#f2a49b;
    --rose-deep:#e8847b;
    --rose-text:#e47f74;
    --ink:#4f4f4f;
    --ink-soft:#6a6a6a;
    --paper:#f5f4f4;
    --white:#ffffff;
    --backdrop:#e6e4e2;
  }
  *{margin:0;padding:0;box-sizing:border-box}
  html,body{width:1200px;height:841px;overflow:hidden}
  body{background:var(--backdrop);font-family:"Open Sans",Arial,sans-serif;color:var(--ink);position:relative}
  h1,h2{font-weight:400}
  .page{position:absolute;top:24px;width:560px;height:792px;background:var(--paper);overflow:hidden;box-shadow:0 2px 10px rgba(0,0,0,.12)}
  .page--front{left:30px}
  .page--back{left:610px}
  .layer{position:absolute;left:0;top:0}
  .brand{position:absolute;top:52px;right:16px;width:240px;text-align:center;color:var(--white);font-weight:300;font-size:17px;letter-spacing:-.2px}

  /* front */
  .front-title{position:absolute;left:16px;top:16px;color:var(--rose-text);font-size:24px;line-height:28px}
  .front-sub{position:absolute;left:16px;top:86px;font-size:15px;color:var(--ink-soft)}
  .hook{position:absolute;top:412px;left:0;width:100%;text-align:center;color:var(--rose-text);font-size:21px;letter-spacing:-.2px}
  .hook-answer{position:absolute;top:446px;left:0;width:100%;text-align:center;color:var(--ink-soft);font-size:19px;font-weight:300}
  .divider{position:absolute;top:480px;left:52px;width:472px;border-top:1px dashed var(--rose)}
  .col{position:absolute;top:496px;width:230px;font-size:10.8px;line-height:14.4px;letter-spacing:-.2px;text-align:justify;color:var(--ink-soft)}
  .col--a{left:36px}
  .col--b{left:300px}
  .col p{margin-bottom:14px}
  .col-head{color:var(--rose-text);font-size:11.6px;margin-bottom:14px !important}
  .callout{background:var(--rose);color:var(--white);font-style:italic;font-weight:600;text-align:center;padding:3px 6px;margin:-3px 0 10px;line-height:15px}
  .offer-band{position:absolute;top:713px;left:0;width:100%;height:46px;background:var(--rose-deep);color:var(--white);font-size:11.4px;line-height:15px;letter-spacing:-.15px;text-align:center;padding-top:8px}
  .contact-row{position:absolute;top:759px;left:0;width:100%;height:33px;display:flex;justify-content:space-around;align-items:center;font-size:11.4px;color:var(--ink)}
  .contact-item{display:flex;align-items:center;gap:5px}

  /* back */
  .question{position:absolute;left:32px;top:300px;color:var(--rose-text);font-size:17px;line-height:22px}
  .answer{position:absolute;left:32px;top:360px;font-size:17.5px;color:var(--ink)}
  .answer b{font-weight:600}
  .yes-box{position:absolute;left:32px;top:397px;width:230px;height:302px;background:var(--rose);padding:12px 6px 0 8px;color:var(--white);font-size:11px;line-height:14.4px;letter-spacing:-.15px}
  .yes-box li{list-style:none;position:relative;padding-left:10px;margin-bottom:15px}
  .yes-box svg{position:absolute;left:0;top:4px}
  .owner{position:absolute;left:40px;top:716px;font-size:11.8px;line-height:17.5px;color:var(--ink);font-style:normal}
  .owner-name{color:var(--rose-text)}
  .help-title{position:absolute;left:295px;top:318px;color:var(--rose-text);font-size:15.5px}
  .help-list{position:absolute;left:295px;top:346px;width:250px;font-size:10.8px;line-height:14.6px;letter-spacing:-.15px;text-align:justify;color:var(--ink)}
  .help-list li{list-style:none}
  .help-list li::before{content:"•";color:var(--rose);margin-right:6px}
  .portrait{position:absolute;left:268px;top:508px;width:292px;height:284px;background:linear-gradient(160deg,#f7f6f5 0%,#ebe4de 55%,#d8cbc1 100%)}
</style>
</head>
<body>

<!-- FRONT -->
<section class="page page--front">
  <svg class="layer" width="560" height="400" viewBox="0 0 560 400" role="img" aria-label="Photo of a smiling baby peeking over a white blanket in a crib">
    <defs>
      <linearGradient id="babyTone" x1="0" y1="0" x2="1" y2="1">
        <stop offset="0" stop-color="#eceae9"/>
        <stop offset=".55" stop-color="#e0d4cc"/>
        <stop offset="1" stop-color="#f3f1f0"/>
      </linearGradient>
    </defs>
    <path d="M0 0H560V345C430 385 210 382 0 332Z" fill="url(#babyTone)"/>
    <path d="M0 332C210 382 430 385 560 345V358C430 398 210 396 0 346Z" fill="var(--white)"/>
  </svg>
  <svg class="layer" width="560" height="130" viewBox="0 0 560 130" aria-hidden="true">
    <path d="M275 0H560V122C470 128 345 120 305 64C292 44 283 20 275 0Z" fill="var(--rose)"/>
  </svg>
  <div class="brand">The Quiet Meadow Nest</div>

  <h1 class="front-title">Is sleep an issue<br>in your home?</h1>
  <p class="front-sub">Sleep, baby, sleep....</p>

  <h2 class="hook">Is your baby having trouble sleeping? ... are you?!</h2>
  <p class="hook-answer">I CAN HELP!</p>
  <div class="divider"></div>

  <div class="col col--a">
    <p class="col-head">Teaching children how to sleep</p>
    <p>The Quiet Meadow Nest is a pediatric sleep consultancy that specializes in helping parents with children who struggle to develop good and healthy sleep habits. Disruptive sleep patterns or not enough sleep can affect the physical, mental and emotional development of your child.</p>
    <p>Of course nobody plans to have a sleep problem, but habits can become easily ingrained and spiral quickly out of control and you can find yourself sleep deprived,</p>
  </div>
  <div class="col col--b">
    <p>desperate and not too sure what to do. You see all the other sleeping babies and wish there was someone who understood what you were going through?! <i><b>Well, there is!</b></i></p>
    <p class="callout">Contact me for a free 15 minute consultation at +34 612 384 705</p>
    <p>This 15 minute „mini“ consultation is a chance to discuss your unique sleep challenges and sleep goals with me. I will provide you with an overview of how I will work with your family to achieve your wildest sleep dreams (goals).</p>
  </div>

  <div class="offer-band">First FREE evaluation call, to the parents, to get to know each other better, learn about<br>their child's particular sleep problems and see if we are a good fit and can work together!</div>

  <div class="contact-row">
    <span class="contact-item">
      <svg width="12" height="12" viewBox="0 0 12 12" aria-hidden="true"><circle cx="6" cy="6" r="6" fill="var(--rose-deep)"/><rect x="3" y="4" width="6" height="4.2" fill="none" stroke="#fff" stroke-width=".9"/><path d="M3 4l3 2.3L9 4" fill="none" stroke="#fff" stroke-width=".9"/></svg>
      info@quietmeadownest-example.com
    </span>
    <span class="contact-item">
      <svg width="12" height="12" viewBox="0 0 12 12" aria-hidden="true"><circle cx="6" cy="6" r="5.4" fill="none" stroke="var(--rose-deep)" stroke-width="1.2"/><path d="M4.2 3.4l1 .9-.5.9c.4.9 1 1.5 1.9 1.9l.9-.5.9 1-.7.9C5.7 8.3 3.8 6.4 3.5 4.1z" fill="var(--rose-deep)"/></svg>
      +34 612 384 705
    </span>
    <span class="contact-item">
      <svg width="12" height="12" viewBox="0 0 12 12" aria-hidden="true"><circle cx="6" cy="6" r="5.4" fill="none" stroke="var(--rose-deep)" stroke-width="1.2"/><circle cx="6" cy="6" r="2.6" fill="var(--rose-deep)"/></svg>
      quietmeadownest-example.com
    </span>
  </div>
</section>

<!-- BACK -->
<section class="page page--back">
  <svg class="layer" width="560" height="320" viewBox="0 0 560 320" role="img" aria-label="Photo of a newborn sleeping peacefully in a white round crib">
    <defs>
      <linearGradient id="cribTone" x1="0" y1="0" x2="1" y2="1">
        <stop offset="0" stop-color="#f1efee"/>
        <stop offset=".45" stop-color="#e6d9d1"/>
        <stop offset="1" stop-color="#ece9e8"/>
      </linearGradient>
    </defs>
    <path d="M0 0H560V300C400 306 190 268 0 186Z" fill="url(#cribTone)"/>
    <path d="M0 186C190 268 400 306 560 300V312C400 318 190 282 0 200Z" fill="var(--white)"/>
  </svg>
  <svg class="layer" width="560" height="130" viewBox="0 0 560 130" aria-hidden="true">
    <path d="M275 0H560V122C470 128 345 120 305 64C292 44 283 20 275 0Z" fill="var(--rose)"/>
  </svg>
  <div class="brand">The Quiet Meadow Nest</div>

  <h2 class="question">Do I need a sleep<br>consultant for my child?</h2>
  <p class="answer">The answer is <b>YES</b> if:</p>

  <ul class="yes-box">
    <li><svg width="7" height="6" viewBox="0 0 7 6" aria-hidden="true"><path d="M.5 3l2 2L6.5.5" fill="none" stroke="#fff" stroke-width="1.1"/></svg>if your child will only fall asleep<br>when nursing or bottle feeding</li>
    <li><svg width="7" height="6" viewBox="0 0 7 6" aria-hidden="true"><path d="M.5 3l2 2L6.5.5" fill="none" stroke="#fff" stroke-width="1.1"/></svg>if your child needs a dummy or other external aid, like being rocked, patted or taken for a care ride to fall asleep</li>
    <li><svg width="7" height="6" viewBox="0 0 7 6" aria-hidden="true"><path d="M.5 3l2 2L6.5.5" fill="none" stroke="#fff" stroke-width="1.1"/></svg>if your good night routine is a challenging and exhausting procedure instead of a relaxed and enjoyable moment for the whole family</li>
    <li><svg width="7" height="6" viewBox="0 0 7 6" aria-hidden="true"><path d="M.5 3l2 2L6.5.5" fill="none" stroke="#fff" stroke-width="1.1"/></svg>if sleep is a constant battle in your home which leaves you feeling frustrated and exhausted</li>
    <li><svg width="7" height="6" viewBox="0 0 7 6" aria-hidden="true"><path d="M.5 3l2 2L6.5.5" fill="none" stroke="#fff" stroke-width="1.1"/></svg>if your own lack of sleep is taking<br>a toll on you and the whole family</li>
  </ul>

  <address class="owner">
    <span class="owner-name">Marta Lindqvist</span><br>
    info@quietmeadownest-example.com<br>
    www.quietmeadownest-example.com<br>
    +34 612 384 705
  </address>

  <h2 class="help-title">What can I do for you?</h2>
  <ul class="help-list">
    <li>Guide you to set an age appropriate foundation for good sleep</li>
    <li>Create an individual sleep plan tailored especially to your child’s sleep needs and circumstances</li>
    <li>Help you to teach your childto go to sleep and get back to sleep independently during the night</li>
    <li>Show you how to teach your child to take healthful, restorative naps</li>
    <li>Learn</li>
  </ul>

  <div class="portrait" role="img" aria-label="Portrait of the sleep consultant holding a smiling toddler"></div>
</section>

</body>
</html>
```